Create a Wordpress Design (Dorrel)

We need a wordpress design for an established auction and real estate company based in Tennessee. The winning design will incorporate a professional color scheme with company logo in a clean layout. The design needs to consider that this will be developed on a responsive theme. Colors are those that will highlight the logo.
Updates

This client, an older gentleman, wants the site to mimic http://www.quillfordbidhouse.example/. If you can adjust you designs with this site in mind - perhaps 3 columns, less color etc. We are trying to get him a concept that he likes and he keeps mentioning this site. Do not copy this site, but keep it in mind while re-doing the concept. Thanks, - auction services -

Industry/Entity Type

Real Estate

Font styles to use
Sans Serif

Colors

Designer to choose colors to be used in the design.

Requirements
Must have
• - Navigation: 1) Home - with auctions as content as seen at http://brenwickgavel.example/ 2) Properties for Sale 3) Auctions 4) Sell Your Property 5) Community Info 6) About Us 7) Contact Us

Color will be those that highlight logo in a professional creative way. Site tagline: "Our Signs are Everywhere". Site will have a slideshow - please use stock real estate image for the initial photo.

Widgets: 1) social media (FB twitter, linked In, Youtube, RSS) 2) News & Events blog, 3) testimonials 4) featured Property widget.

Footer will have contact info (below) smaller company logo, and the association logos attached, and contact info:
Phone: (615) 555-0178
Contacts: Marion Teague-Hollis
Email: marketing@kenwoodorrel.example
Address: 22-C Elmfield Court W, Murfreesboro, TN 37199

Nice to have
• use and styling of a dropdown menu: Under AUCTIONS, 1) Upcoming 2) Past

```html
<!DOCTYPE html>
<html lang="en">
<head>
<meta charset="utf-8">
<title>Dorrel Commercial Realtors, Auctioneers LLC</title>
<link href="https://fonts.googleapis.com/css2?family=Jost:wght@400;500;600&display=swap" rel="stylesheet">
<style>
:root{
  --red:#b3121f;
  --red-dark:#8e0b16;
  --red-text:#c0182a;
  --ink:#1e1e1e;
  --body:#3a3a3a;
  --muted:#6a6a6a;
  --page:#e9e9e9;
  --panel:#f4f4f4;
  --card:#ffffff;
  --line:#d6d6d6;
  --footer:#ffffff;
}
*{box-sizing:border-box;margin:0;padding:0}
html,body{width:1200px;height:2542px;overflow:hidden}
body{font-family:"Jost",sans-serif;background:var(--page);color:var(--body);position:relative}
.top-band{position:absolute;left:0;top:0;width:1200px;height:240px;background:linear-gradient(#b8131f,#a20f1a)}
.white-band{position:absolute;left:0;top:240px;width:1200px;height:170px;background:linear-gradient(#fff,var(--page))}
.topbar{position:absolute;right:172px;top:14px;display:flex;gap:18px;color:#fff;font-size:13px;align-items:center}
.topbar span{display:flex;align-items:center;gap:6px}
.header{position:absolute;left:170px;top:48px;width:857px;height:80px;background:linear-gradient(#fff,#ececec);display:flex;align-items:center}
.brand{width:170px;display:flex;align-items:center;justify-content:center;gap:6px;font-size:28px;font-weight:600;color:var(--red);letter-spacing:1px}
.brand i{width:12px;height:12px;border-radius:50%;background:var(--red);display:block}
.nav{display:flex;height:100%;margin-left:10px}
.nav a{display:flex;align-items:center;padding:0 13px;font-size:11.5px;font-weight:500;color:#333;text-decoration:none;border-left:1px solid #dcdcdc;text-transform:uppercase}
.nav a:first-child{border-left:0;color:var(--red-text)}
.slider{position:absolute;left:170px;top:127px;width:857px;height:470px;background:linear-gradient(160deg,#8da0a6 0%,#b9b49a 35%,#a77a68 60%,#6b8a47 100%)}
.slider .caption{position:absolute;left:37px;top:168px;width:350px;background:rgba(15,15,15,.88);padding:14px 14px 12px}
.caption .l1{color:#fff;font-size:25px;font-weight:500;line-height:1.1;letter-spacing:.5px}
.caption .l2{color:#e0192b;font-size:33px;font-weight:500;line-height:1.1;letter-spacing:.5px}
.dots{position:absolute;left:19px;bottom:16px;display:flex;gap:9px}
.dots b{width:13px;height:13px;border-radius:50%;background:#fff;display:block}
.dots b:first-child{background:var(--red)}
.section-title{position:absolute;left:171px;top:640px;font-size:20px;font-weight:500;color:var(--ink)}
.auctions{position:absolute;left:170px;top:681px;width:567px}
.auction{background:var(--panel);border:1px solid var(--line);border-radius:3px;margin-bottom:35px;height:367px}
.auction-head{height:48px;background:linear-gradient(#fff,#e8e8e8);border-bottom:2px solid #cfcfcf;display:flex;align-items:center;padding-left:15px;font-size:16px;font-weight:500;letter-spacing:1px;color:var(--ink)}
.auction-body{display:flex;padding:20px 15px 0}
.media{width:161px}
.thumb{width:161px;height:141px;background:linear-gradient(#8fa3b6,#b5b0a2 60%,#5f7a4c)}
.links{margin-top:10px}
.links a{display:flex;align-items:center;height:31px;margin-bottom:7px;background:linear-gradient(#fafafa,#e2e2e2);color:#333;font-size:15px;text-decoration:none;padding-left:14px;gap:30px}
.info{margin-left:14px;width:362px}
.blurb,.details{background:var(--card);border:1px solid #e2e2e2;padding:8px 10px}
.blurb{height:110px}
.blurb h3{font-size:13.5px;font-weight:600;color:var(--red-text);line-height:1.4}
.blurb p,.details p{font-size:11px;line-height:1.7;color:var(--body)}
.details{margin-top:10px;height:156px;padding-top:12px}
.details h4{font-size:11px;font-weight:600;color:var(--red-text);margin-bottom:4px}
.btn{display:inline-flex;align-items:center;gap:6px;background:var(--red);color:#fff;font-size:12.5px;font-weight:600;padding:6px 10px;border-radius:4px;margin-top:6px;text-decoration:none}
.sidebar{position:absolute;left:752px;top:640px;width:277px}
.widget{background:var(--panel);border:1px solid var(--line);border-radius:3px;margin-bottom:24px}
.widget-head{height:46px;display:flex;align-items:center;justify-content:space-between;padding:0 12px;font-size:15px;font-weight:500;letter-spacing:.5px;color:var(--ink);text-transform:uppercase;background:linear-gradient(#fff,#ececec);border-bottom:2px solid #cfcfcf}
.widget-head .arrows{font-size:14px;letter-spacing:4px}
.widget-body{padding:12px 12px 14px}
.featured{height:394px}
.photo{width:251px;background:linear-gradient(#3f6d8f,#8aa1ad 55%,#4b7b59)}
.widget h3{font-size:13px;font-weight:600;color:var(--red-text);line-height:1.45;margin-top:12px}
.widget h4{font-size:13px;font-weight:600;color:var(--ink);margin-top:12px}
.widget p{font-size:11.5px;line-height:1.7;color:var(--body)}
.widget .btn{margin-top:8px}
.news{height:827px}
.post{margin-bottom:20px}
.post .meta{font-size:11px;color:var(--muted);margin-top:10px}
.post h3{margin-top:2px}
.testimonial{height:340px}
.who{display:flex;align-items:center;gap:12px}
.avatar{width:104px;height:104px;border-radius:50%;background:linear-gradient(#c9d4dc,#8d9aa3)}
.who strong{display:block;font-size:17px;font-weight:500;color:var(--red-text)}
.who span{font-size:12px;color:var(--muted)}
.quote{font-size:38px;line-height:.8;color:#333;margin-top:6px;font-weight:600}
.testimonial p{font-size:12.5px;line-height:1.85}
.footer{position:absolute;left:0;top:2288px;width:1200px;height:254px;background:var(--footer)}
.footer-inner{position:absolute;left:176px;top:36px;display:flex}
.footer-brand{width:180px;display:flex;align-items:center;gap:6px;font-size:28px;font-weight:600;color:#777;height:60px;margin-top:14px}
.footer-brand i{width:12px;height:12px;border-radius:50%;background:#777;display:block}
.footer h5{font-size:12px;font-weight:500;color:var(--red-text);letter-spacing:.5px;margin-bottom:16px}
.contact{width:188px}
.contact p{font-size:11.5px;line-height:2.05;color:var(--ink)}
.assoc{width:330px}
.badges{display:flex;gap:3px;background:#e6e6e6;padding:4px;width:298px}
.badges b{height:22px;flex:1;background:#9a9a9a;display:block;border-radius:2px}
.social .icons{display:flex;gap:5px}
.social .icons b{width:26px;height:26px;border-radius:50%;background:#8a8a8a;display:block}
.copyright{position:absolute;left:0;width:1200px;top:220px;text-align:center;font-size:11.5px;color:var(--ink)}
</style>
</head>
<body>
<div class="top-band"></div>
<div class="white-band"></div>

<div class="topbar">
  <span><svg width="12" height="12" viewBox="0 0 12 12"><path d="M3 1l2 3-1 1c.7 1.4 1.6 2.3 3 3l1-1 3 2-1 2C5 11 1 7 1 2z" fill="#fff"/></svg>kenwood@kenwoodorrel.example</span>
  <span><svg width="13" height="10" viewBox="0 0 13 10"><rect x=".5" y=".5" width="12" height="9" fill="none" stroke="#fff"/><path d="M1 1l5.5 4.5L12 1" fill="none" stroke="#fff"/></svg>Phone: 615.555.0178</span>
</div>

<header class="header">
  <div class="brand"><i></i>DORREL</div>
  <nav class="nav">
    <a>Home</a><a>Properties for Sale</a><a>Auctions</a><a>Sell Your Property</a><a>Community Info</a><a>About Us</a><a>Contact Us</a>
  </nav>
</header>

<section class="slider" role="img" aria-label="Stock photo of a smiling couple in front of a suburban house">
  <div class="caption">
    <div class="l1">DORREL COMMERCIAL REALTORS,</div>
    <div class="l2">AUCTIONEERS LLC</div>
  </div>
  <div class="dots"><b></b><b></b><b></b><b></b></div>
</section>

<h2 class="section-title">AUCTIONS</h2>

<main class="auctions">
  <article class="auction">
    <div class="auction-head">AUCTIONS&nbsp; 1</div>
    <div class="auction-body">
      <div class="media">
        <div class="thumb" role="img" aria-label="Photo of a modern glass house at dusk"></div>
        <div class="links">
          <a><svg width="16" height="14" viewBox="0 0 16 14"><rect x="1" y="3" width="14" height="10" rx="2" fill="#444"/><circle cx="8" cy="8" r="3" fill="#eee"/><rect x="5" y="1" width="6" height="3" fill="#444"/></svg>Photos</a>
          <a><svg width="16" height="14" viewBox="0 0 16 14"><rect x="2" y="1" width="12" height="12" fill="#444"/><rect x="5" y="3" width="6" height="8" fill="#eee"/></svg>Videos</a>
          <a><svg width="16" height="14" viewBox="0 0 16 14"><path d="M4 1h6l3 3v9H4z" fill="none" stroke="#444" stroke-width="1.5"/></svg>Details</a>
        </div>
      </div>
      <div class="info">
        <div class="blurb"><h3>Lorem Ipsum is simply dummy text of the printing and typesetting industry.</h3><p>Lorem Ipsum has been the industry's standard dummy text ever since the 1500s, when an unknown printer took a galley of type and scrambled it to make a type specimen book.</p></div>
        <div class="details"><h4>Live On-Site Auction with Online Bidding</h4><p>Begins:&nbsp; Thursday, May 24, 2018 at 6:00 AM EDT<br>Ends:&nbsp; Sunday, May 27, 2018 at 6:00 AM EDT<br>Location: P.O. Box 40417, Roanoke, VA 24099</p><a class="btn"><svg width="14" height="14" viewBox="0 0 14 14"><path d="M2 12l6-6M6 2l5 5M8 1l5 5" stroke="#fff" stroke-width="2"/></svg>Click here for Online Bidding</a></div>
      </div>
    </div>
  </article>

  <article class="auction">
    <div class="auction-head">AUCTIONS&nbsp; 2</div>
    <div class="auction-body">
      <div class="media">
        <div class="thumb" role="img" aria-label="Photo of a stone house with a garage"></div>
        <div class="links">
          <a><svg width="16" height="14" viewBox="0 0 16 14"><rect x="1" y="3" width="14" height="10" rx="2" fill="#444"/><circle cx="8" cy="8" r="3" fill="#eee"/><rect x="5" y="1" width="6" height="3" fill="#444"/></svg>Photos</a>
          <a><svg width="16" height="14" viewBox="0 0 16 14"><rect x="2" y="1" width="12" height="12" fill="#444"/><rect x="5" y="3" width="6" height="8" fill="#eee"/></svg>Videos</a>
          <a><svg width="16" height="14" viewBox="0 0 16 14"><path d="M4 1h6l3 3v9H4z" fill="none" stroke="#444" stroke-width="1.5"/></svg>Details</a>
        </div>
      </div>
      <div class="info">
        <div class="blurb"><h3>Lorem Ipsum is simply dummy text of the printing and typesetting industry.</h3><p>Lorem Ipsum has been the industry's standard dummy text ever since the 1500s, when an unknown printer took a galley of type and scrambled it to make a type specimen book.</p></div>
        <div class="details"><h4>Live On-Site Auction with Online Bidding</h4><p>Begins:&nbsp; Thursday, May 24, 2018 at 6:00 AM EDT<br>Ends:&nbsp; Sunday, May 27, 2018 at 6:00 AM EDT<br>Location: P.O. Box 40417, Roanoke, VA 24099</p><a class="btn"><svg width="14" height="14" viewBox="0 0 14 14"><path d="M2 12l6-6M6 2l5 5M8 1l5 5" stroke="#fff" stroke-width="2"/></svg>Click here for Online Bidding</a></div>
      </div>
    </div>
  </article>

  <article class="auction">
    <div class="auction-head">AUCTIONS&nbsp; 3</div>
    <div class="auction-body">
      <div class="media">
        <div class="thumb" role="img" aria-label="Photo of a family outside a two-storey house"></div>
        <div class="links">
          <a><svg width="16" height="14" viewBox="0 0 16 14"><rect x="1" y="3" width="14" height="10" rx="2" fill="#444"/><circle cx="8" cy="8" r="3" fill="#eee"/><rect x="5" y="1" width="6" height="3" fill="#444"/></svg>Photos</a>
          <a><svg width="16" height="14" viewBox="0 0 16 14"><rect x="2" y="1" width="12" height="12" fill="#444"/><rect x="5" y="3" width="6" height="8" fill="#eee"/></svg>Videos</a>
          <a><svg width="16" height="14" viewBox="0 0 16 14"><path d="M4 1h6l3 3v9H4z" fill="none" stroke="#444" stroke-width="1.5"/></svg>Details</a>
        </div>
      </div>
      <div class="info">
        <div class="blurb"><h3>Lorem Ipsum is simply dummy text of the printing and typesetting industry.</h3><p>Lorem Ipsum has been the industry's standard dummy text ever since the 1500s, when an unknown printer took a galley of type and scrambled it to make a type specimen book.</p></div>
        <div class="details"><h4>Live On-Site Auction with Online Bidding</h4><p>Begins:&nbsp; Thursday, May 24, 2018 at 6:00 AM EDT<br>Ends:&nbsp; Sunday, May 27, 2018 at 6:00 AM EDT<br>Location: P.O. Box 40417, Roanoke, VA 24099</p><a class="btn"><svg width="14" height="14" viewBox="0 0 14 14"><path d="M2 12l6-6M6 2l5 5M8 1l5 5" stroke="#fff" stroke-width="2"/></svg>Click here for Online Bidding</a></div>
      </div>
    </div>
  </article>

  <article class="auction">
    <div class="auction-head">AUCTIONS&nbsp; 4</div>
    <div class="auction-body">
      <div class="media">
        <div class="thumb" role="img" aria-label="Photo of a house under construction"></div>
        <div class="links">
          <a><svg width="16" height="14" viewBox="0 0 16 14"><rect x="1" y="3" width="14" height="10" rx="2" fill="#444"/><circle cx="8" cy="8" r="3" fill="#eee"/><rect x="5" y="1" width="6" height="3" fill="#444"/></svg>Photos</a>
          <a><svg width="16" height="14" viewBox="0 0 16 14"><rect x="2" y="1" width="12" height="12" fill="#444"/><rect x="5" y="3" width="6" height="8" fill="#eee"/></svg>Videos</a>
          <a><svg width="16" height="14" viewBox="0 0 16 14"><path d="M4 1h6l3 3v9H4z" fill="none" stroke="#444" stroke-width="1.5"/></svg>Details</a>
        </div>
      </div>
      <div class="info">
        <div class="blurb"><h3>Lorem Ipsum is simply dummy text of the printing and typesetting industry.</h3><p>Lorem Ipsum has been the industry's standard dummy text ever since the 1500s, when an unknown printer took a galley of type and scrambled it to make a type specimen book.</p></div>
        <div class="details"><h4>Live On-Site Auction with Online Bidding</h4><p>Begins:&nbsp; Thursday, May 24, 2018 at 6:00 AM EDT<br>Ends:&nbsp; Sunday, May 27, 2018 at 6:00 AM EDT<br>Location: P.O. Box 40417, Roanoke, VA 24099</p><a class="btn"><svg width="14" height="14" viewBox="0 0 14 14"><path d="M2 12l6-6M6 2l5 5M8 1l5 5" stroke="#fff" stroke-width="2"/></svg>Click here for Online Bidding</a></div>
      </div>
    </div>
  </article>
</main>

<aside class="sidebar">
  <section class="widget featured">
    <div class="widget-head">Featured Property <span class="arrows">‹›</span></div>
    <div class="widget-body">
      <div class="photo" style="height:148px" role="img" aria-label="Photo of a modern house with a pool at dusk"></div>
      <h3>Lorem Ipsum is simply dummy text of the printing and typesetting industry.</h3>
      <h4>Live On-Site Auction with Online Bidding</h4>
      <p>Begins:&nbsp; Thursday, May 24, 2018 at 6:00 AM EDT<br>Ends:&nbsp; Sunday, May 27, 2018 at 6:00 AM EDT<br>Location: P.O. Box 40417, Roanoke, VA 24099</p>
      <a class="btn" style="padding:7px 18px">View Details</a>
    </div>
  </section>

  <section class="widget news">
    <div class="widget-head">News &amp; Events Blog</div>
    <div class="widget-body" style="padding-top:24px">
      <div class="post">
        <div class="photo" style="height:173px" role="img" aria-label="Photo of a lit modern house with a terrace at night"></div>
        <div class="meta">Posted By 20-7-2014</div>
        <h3>Lorem Ipsum is simply dummy text of the printing and typesetting industry.</h3>
        <p>Lorem Ipsum has been the industry's standard dummy text ever since the 1500s, when an known printer took a galley of type and scrambled it to make a type specimen book.</p>
        <a class="btn">Read More</a>
      </div>
      <div class="post" style="margin-top:26px">
        <div class="photo" style="height:173px" role="img" aria-label="Photo of a modern house on a lawn at twilight"></div>
        <div class="meta">Posted By 20-7-2014</div>
        <h3>Lorem Ipsum is simply dummy text of the printing and typesetting industry.</h3>
        <p>Lorem Ipsum has been the industry's standard dummy text ever since the 1500s, when an known printer took a galley of type and scrambled it to make a type specimen book.</p>
        <a class="btn">Read More</a>
      </div>
    </div>
  </section>

  <section class="widget testimonial">
    <div class="widget-head">Testimonials <span class="arrows">‹›</span></div>
    <div class="widget-body">
      <div class="who">
        <div class="avatar" role="img" aria-label="Portrait photo of the client"></div>
        <div><strong>Graham Whitley</strong><span>Company Name</span></div>
      </div>
      <div class="quote">“</div>
      <p>Lorem ipsum dolor sit amet, consectetur adipisicing elit, sed do eiusmod tempor incididunt ut labore et dolore magna aliqua. Ut enim ad minim veniam, quis nostrud exercitation ullamco laboris nisi ut aliquip ex ea commodo consequat.</p>
    </div>
  </section>
</aside>

<footer class="footer">
  <div class="footer-inner">
    <div class="footer-brand"><i></i>DORREL</div>
    <div class="contact">
      <h5>CONTACT INFO</h5>
      <p>Phone: (615) 555-0178<br>Contacts: Marion Teague-Hollis<br>Email: marketing@kenwoodorrel.example<br>Address: 22-C Elmfield Court W,<br>Murfreesboro, TN 37199</p>
    </div>
    <div class="assoc">
      <h5>ASSOCIATION LOGOS</h5>
      <div class="badges"><b></b><b></b><b></b><b></b><b></b><b></b><b></b><b></b></div>
    </div>
    <div class="social">
      <h5>SOCIAL LINKS</h5>
      <div class="icons"><b></b><b></b><b></b><b></b><b></b></div>
    </div>
  </div>
  <div class="copyright">© 2014 Company Name ,All Rights Reserved</div>
</footer>
</body>
</html>
```